Harrow Tavern & Grille Menu Makeover

I am looking for a professional look to update our current menu. We are an independently owned sports bar and grill. Up to this point, I have done all of my own graphic designing. I am looking for something classy/family oriented. We are a very family friendly sports bar that offers a wide variety of menu options. Our website is www.harrowtavernco.example. This may help you get more of a feel for what type of place we are and what we offer. Our menu is listed on the website. My current menu is 8.5x14 inserts that feature a cover page, 4 inside pages and a back page. I would like something a little more condensed than this. Possibly a large tri-fold menu? I am open to all new ideas. I do have some pictures on my menu now, and would like to continue using a few pictures to feature some of my items. I would like something that is in a format that gives me the option to change items and prices on my own in the future. I would also like it to feature, or inform my patrons about our technology that we offer. We offer online ordering and we are a "verified venue" with Brewvoke.( a social site for craft beer lovers).

Industry/Entity Type

Sports Bar

Requirements
Nice to have
• Nice to have some pictures, but does not have to. We do feature 9 different beers on tap. A lot of them are local craft beers from the state of Kansas. Not sure if that is something we can feature, but it is a nice talking point. All of our tables and bar are hand built. With a rich mahogany finish on all of our woodwork, some type of "woodgrain" look into the menu would be nice.

```html
<!DOCTYPE html>
<html lang="en">
<head>
<meta charset="UTF-8">
<title>Harrow Tavern &amp; Grille — Menu</title>
<link href="https://fonts.googleapis.com/css2?family=Bebas+Neue&family=Oswald:wght@300;400&family=Playfair+Display:wght@400;700&family=Montserrat:wght@700&display=swap" rel="stylesheet">
<style>
  :root {
    --page: #121417;
    --panel: #0b0c0e;
    --gold: #e2c47a;
    --gold-deep: #c9a657;
    --gold-text: #d9c07e;
    --cream: #efe6cf;
    --greens: #4a5a33;
  }
  * { box-sizing: border-box; margin: 0; padding: 0; }
  html, body { width: 850px; height: 1200px; overflow: hidden; background: var(--page); }
  .menu {
    position: relative;
    width: 850px;
    height: 1200px;
    background: var(--page);
    overflow: hidden;
  }
  .hero-photo {
    position: absolute;
    left: 0; top: 120px;
    width: 850px; height: 240px;
    background:
      radial-gradient(ellipse 150px 70px at 425px 150px, #e9e6dc 0%, #bdb9ae 45%, rgba(60,58,52,0) 100%),
      radial-gradient(ellipse 220px 110px at 200px 150px, rgba(214,196,130,.85) 0%, rgba(120,110,70,.5) 50%, rgba(18,20,23,0) 100%),
      radial-gradient(ellipse 220px 110px at 660px 140px, rgba(220,204,150,.8) 0%, rgba(120,110,70,.45) 50%, rgba(18,20,23,0) 100%),
      radial-gradient(ellipse 160px 60px at 120px 200px, rgba(74,90,51,.7) 0%, rgba(18,20,23,0) 100%),
      linear-gradient(180deg, var(--page) 0%, rgba(18,20,23,0) 30%, rgba(18,20,23,0) 75%, var(--page) 100%);
  }
  .brand {
    position: absolute;
    top: 82px; left: 0; width: 850px;
    text-align: center;
    font-family: 'Playfair Display', serif;
    font-weight: 400;
    font-size: 42px;
    color: var(--gold);
    letter-spacing: 1px;
  }
  .panel {
    position: absolute;
    left: 68px; top: 312px;
    width: 712px; height: 808px;
    background: var(--panel);
    border-radius: 12px;
    box-shadow: 0 0 30px rgba(0,0,0,.6);
  }
  .section-title {
    position: absolute;
    left: 94px;
    font-family: 'Playfair Display', serif;
    font-weight: 700;
    font-size: 35px;
    color: var(--gold);
    letter-spacing: .5px;
  }
  .col {
    position: absolute;
    width: 322px;
    display: flex;
    flex-direction: column;
  }
  .item { margin-bottom: 9px; }
  .item-name {
    font-family: 'Bebas Neue', sans-serif;
    font-size: 17.5px;
    line-height: 17px;
    color: var(--gold);
  }
  .item-desc {
    font-family: 'Oswald', sans-serif;
    font-weight: 300;
    font-size: 8.6px;
    line-height: 12px;
    text-transform: uppercase;
    color: var(--gold-text);
  }
  .item-price {
    font-family: 'Montserrat', sans-serif;
    font-weight: 700;
    font-size: 5.8px;
    letter-spacing: .8px;
    line-height: 9px;
    text-transform: uppercase;
    color: var(--gold-deep);
  }
  .divider { position: absolute; left: 190px; top: 760px; }
</style>
</head>
<body>
<main class="menu">
  <div class="hero-photo" role="img" aria-label="Photo of grilled quesadilla wedges around a cup of sour cream dip"></div>
  <div class="brand">Harrow Tavern &amp; Grille</div>

  <div class="panel"></div>

  <h2 class="section-title" style="top:332px;">APPETIZERS</h2>

  <div class="col" style="left:98px; top:382px;">
    <div class="item"><div class="item-name">Slider Burgers</div><div class="item-desc">Six juicy bite sized burgers topped with American cheese and served with pickle slices.</div><div class="item-price">8.99</div></div>
    <div class="item"><div class="item-name">Loaded Potato Skins</div><div class="item-desc">Six crispy skins loaded with jack, cheddar and mozzarella cheese, then topped with smoked bacon and green onions. Served with sour cream.</div><div class="item-price">8.99</div></div>
    <div class="item"><div class="item-name">Rattlesnake Eggs</div><div class="item-desc">A spicy combo of pepper jack cheese and jalapeños, battered and fried.</div><div class="item-price">7.99</div></div>
    <div class="item"><div class="item-name">Mozzarella Cheese Sticks</div><div class="item-desc">Classic battered mozzarella cheese sticks served with ranch dressing.</div><div class="item-price">7.99</div></div>
    <div class="item"><div class="item-name">Grand Slam French Fries</div><div class="item-desc">French fries loaded with jack, cheddar, mozzarella, bacon, jalapeños and green onions! Served with ranch dressing.</div><div class="item-price">7.99</div></div>
    <div class="item"><div class="item-name">Bang Bang Shrimp</div><div class="item-desc">Lightly breaded and fried shrimp coated with a spicy Thai sauce, topped with parmesan cheese and diced tomatoes. Served over a bed of romaine lettuce.</div><div class="item-price">7.99</div></div>
    <div class="item"><div class="item-name">Ballpark Pretzel Basket</div><div class="item-desc">Buttered and salted pretzels served with nacho cheese sauce.</div><div class="item-price">7.99</div></div>
  </div>

  <div class="col" style="left:427px; top:382px;">
    <div class="item"><div class="item-name">Spicy Southwest Chicken Eggrolls</div><div class="item-desc">Stuffed with black beans, corn and chicken. Served with southwest ranch.</div><div class="item-price">9.99</div></div>
    <div class="item"><div class="item-name">Blooming Onion</div><div class="item-desc">This fan favorite is classically carved and deep fried to perfection. Served with Harrow signature dipping sauce.</div><div class="item-price">7.99</div></div>
    <div class="item"><div class="item-name">Chicken Quesadilla</div><div class="item-desc">A 12 inch flour tortilla stuffed with grilled chicken and jack and cheddar cheese. Served with salsa.</div><div class="item-price">8.99</div></div>
    <div class="item"><div class="item-name">Hank's Boneless Buffalo Wings</div><div class="item-desc">A full pound of spicy, boneless buffalo wings. Served with ranch dressing or Hank's gold label sauce.</div><div class="item-price">7.99</div></div>
    <div class="item"><div class="item-name">Harrow Loaded Nachos</div><div class="item-desc">Tri-colored tortilla chips smothered with creamy Monterey jack cheese, choice of beef or chicken, and topped with grilled peppers and onions, jalapeños and diced tomatoes. Served with sour cream and salsa.</div><div class="item-price">9.99</div></div>
    <div class="item"><div class="item-name">Garlic Bread Basket</div><div class="item-desc">Tri-colored tortilla chips smothered with creamy Monterey jack cheese, choice of beef or chicken, and topped with grilled peppers and onions, jalapeños and diced tomatoes. Served with sour cream and salsa.</div><div class="item-price">9.99</div></div>
  </div>

  <svg class="divider" width="470" height="20" viewBox="0 0 470 20" aria-hidden="true">
    <defs>
      <linearGradient id="rule" x1="0" x2="1">
        <stop offset="0" stop-color="#e2c47a" stop-opacity="0"/>
        <stop offset=".5" stop-color="#e2c47a"/>
        <stop offset="1" stop-color="#e2c47a" stop-opacity="0"/>
      </linearGradient>
    </defs>
    <rect x="0" y="9.5" width="470" height="1.2" fill="url(#rule)"/>
    <rect x="228" y="3" width="10" height="10" transform="rotate(45 233 8)" fill="none" stroke="#e2c47a" stroke-width="1.4"/>
  </svg>

  <h2 class="section-title" style="top:798px;">SALADS</h2>

  <div class="col" style="left:98px; top:846px;">
    <div class="item"><div class="item-name">Chicken Tender Garden Salad</div><div class="item-desc">A spring lettuce mix topped with shredded jack and cheddar cheese, garden vegetables, bacon, croutons and egg. With your choice of crispy or grilled chicken.</div><div class="item-price">Large 8.99 / Small 7.99</div></div>
    <div class="item"><div class="item-name">Nacho Crunchito Salad</div><div class="item-desc">Harrow's unique blend of iceberg lettuce, topped with jack and cheddar cheese, tomatoes, black olives, ranch style beans and creamy Italian dressing. Topped with Crunchito chips.</div><div class="item-price">Large 8.99 / Small 7.99</div></div>
    <div class="item"><div class="item-name">Cobb Salad</div><div class="item-desc">Rows of ham, turkey and roast beef, side by side with baby corn, jack and cheddar cheese, egg slices, garden vegetables, bacon and croutons served over iceberg lettuce.</div><div class="item-price">Large 8.99 / Small 7.99</div></div>
    <div class="item"><div class="item-name">Summer Berry Salad</div><div class="item-desc">A blend of fresh berries, tomatoes, croutons, mandarin oranges and crumbled feta cheese served on fresh spinach leaves. Your choice of chicken or shrimp.</div><div class="item-price">Large 8.99 / Small 7.99</div></div>
  </div>

  <div class="col" style="left:427px; top:846px;">
    <div class="item"><div class="item-name">House Caesar Salad</div><div class="item-desc">A classic mix of crisp romaine lettuce, shredded parmesan cheese, and croutons. Served with our signature Caesar dressing.</div><div class="item-price">Large 6.99 / Small 5.99<br>Large with chicken 8.99 / Small with chicken 6.99</div></div>
    <div class="item"><div class="item-name">Nacho Crunchito Salad</div><div class="item-desc">Harrow's unique blend of iceberg lettuce, topped with jack and cheddar cheese, tomatoes, black olives, ranch style beans and creamy Italian dressing. Topped with Crunchito chips.</div><div class="item-price">Large 8.99 / Small 7.99</div></div>
    <div class="item"><div class="item-name">Cobb Salad</div><div class="item-desc">Rows of ham, turkey and roast beef, side by side with baby corn, jack and cheddar cheese, egg slices, garden vegetables, bacon and croutons served over iceberg lettuce.</div><div class="item-price">Large 8.99 / Small 7.99</div></div>
    <div class="item"><div class="item-name">Summer Berry Salad</div><div class="item-desc">A blend of fresh berries, tomatoes, croutons, mandarin oranges and crumbled feta cheese served on fresh spinach leaves. Your choice of chicken or shrimp.</div><div class="item-price">Large 8.99 / Small 7.99</div></div>
  </div>
</main>
</body>
</html>
```